Business card design needed

Family General Practitioner/ Family Physician.
Logo is the logo of the Noble Guild of Family Healers Oceania
http://kpltw.varendo.example/ImageShelf/marks/pages/NGFHO%20mark_jpg.htm
Updates

Project Deadline Extended
Reason: Just a bit more time to make changes and the weekend for me to look at things closely and to choose. Thanks, Orin

Thanks for all the submissions. So many of them are really works of art. Not one of them are not good. The ones that I am eliminating are the ones that I think are not suitable for me personally only, and because if I don't, it makes it very difficult to decide as many of you are also sending me slight variations of a card. I have just decided to choose a second place card too. Can't thank you all enough. Good luck, Orin. P.S - Working today till 10 pm as the card says :-), so probably won't be able to give a feedback till late Saturday night or Sunday morning here in Sydney, Australia. 

Project Deadline Extended
Reason: Just added a second place to the budget and realised that Australia is ahead of the rest of the world in the time zone (only :-) - don't want to offend anyone or start a debate!! ) , so Monday deadline will mean it will be a weekend for the rest of the world. Just wanted to give everyone more time to submit their best, especially since I will be picking a second card too. Can't thank everyone enough for the submissions. P.S - Not keen on photos on the card.

Industry/Entity Type

Business

Contact Information for Business Card

Dr. Orin Halvey M.B.B.S., F.N.G.F.H.O
Family General Practitioner
Address, timings, phone and fax number on the back.

Requirements
Must have
• Timings
Mon 7 am - 7 pm
Tues 7 am - 12 pm
Wed 7 am - 10 pm
Thurs 7 am - 12 pm
Fri 7 am - 8 pm
Sat 8 am - 10 pm
Sun - Off

```html
<!DOCTYPE html>
<html lang="en">
<head>
<meta charset="utf-8">
<title>Dr. Orin Halvey – Business Card</title>
<link rel="stylesheet" href="https://fonts.googleapis.com/css2?family=Montserrat:wght@300;400&display=swap">
<style>
  :root {
    --bg-top: #ffffff;
    --bg-bottom: #ebebeb;
    --card-light: #f2f7fc;
    --card-mid: #b9d8f1;
    --card-deep: #56a8e0;
    --band-light: #d3e7f7;
    --band-deep: #4aa5e0;
    --ink-navy: #1d4a7c;
    --ink-blue: #4f82c2;
    --ink-dark: #1b2b3c;
    --accent-orange: #e07b22;
    --card-edge: #3b4a58;
  }
  * { margin: 0; padding: 0; box-sizing: border-box; }
  html, body { width: 1200px; height: 766px; overflow: hidden; }
  body {
    position: relative;
    background: radial-gradient(ellipse at 50% 35%, var(--bg-top) 0%, var(--bg-bottom) 100%);
    font-family: "Montserrat", sans-serif;
    font-weight: 300;
  }
  .card {
    position: absolute;
    border: 1px solid var(--card-edge);
    box-shadow: 0 2px 5px rgba(0,0,0,0.25);
    overflow: hidden;
  }
  .card-front {
    left: 20px; top: 18px; width: 632px; height: 391px;
    background: linear-gradient(180deg, var(--card-light) 0%, var(--card-mid) 60%, var(--card-deep) 100%);
    color: var(--ink-navy);
    text-align: center;
  }
  .doctor-name {
    position: absolute; left: 0; right: 0; top: 135px;
    font-size: 57px; font-weight: 300; letter-spacing: 0.5px;
    text-shadow: 0 2px 3px rgba(255,255,255,0.7);
  }
  .credentials {
    position: absolute; left: 0; right: 0; top: 196px;
    font-size: 25px; font-weight: 300;
  }
  .specialty {
    position: absolute; left: 0; right: 0; top: 305px;
    font-size: 28px; font-weight: 300;
  }
  .card-back {
    left: 546px; top: 351px; width: 631px; height: 390px;
    background: linear-gradient(180deg, var(--card-light) 0%, #dbeaf7 55%, var(--card-mid) 100%);
  }
  .guild-mark {
    position: absolute; left: 24px; top: 24px; width: 260px; height: 240px;
    display: flex; flex-direction: column; align-items: center; justify-content: center; gap: 14px;
    text-align: center;
  }
  .guild-mark .mark-dot {
    width: 70px; height: 70px; border-radius: 50%;
    background: var(--ink-navy);
  }
  .guild-mark .mark-name {
    font-size: 18px; font-weight: 400; color: var(--ink-navy); line-height: 1.35;
  }
  .hours-title {
    position: absolute; right: 41px; top: 20px;
    font-size: 32px; font-weight: 300; color: var(--ink-navy);
  }
  .hours-table {
    position: absolute; left: 326px; top: 76px; width: 264px;
    border-collapse: collapse;
    font-size: 20px;
  }
  .hours-table td { height: 28.8px; padding: 0; white-space: nowrap; }
  .hours-table .day { color: var(--ink-blue); width: 124px; }
  .hours-table .sep { color: var(--ink-dark); width: 20px; }
  .hours-table .time { color: var(--ink-dark); text-align: right; }
  .contact-band {
    position: absolute; left: 0; right: 0; top: 290px; bottom: 0;
    border-top: 1px solid #8aa6c0;
    background: linear-gradient(180deg, var(--band-light) 0%, var(--band-deep) 100%);
    color: var(--ink-dark);
    font-size: 14px; font-weight: 400;
  }
  .contact-icon { position: absolute; }
  .icon-home { left: 22px; top: 16px; }
  .icon-phone { left: 27px; top: 56px; }
  .address { position: absolute; left: 60px; top: 14px; line-height: 20px; }
  .phones { position: absolute; left: 60px; top: 62px; word-spacing: 2px; }
  .phones span + span { margin-left: 16px; }
</style>
</head>
<body>

  <section class="card card-front">
    <h1 class="doctor-name">Dr. Orin Halvey</h1>
    <p class="credentials">M.B.B.S., F.N.G.F.H.O</p>
    <p class="specialty">Family General Practitioner</p>
  </section>

  <section class="card card-back">
    <div class="guild-mark">
      <span class="mark-dot"></span>
      <span class="mark-name">Noble Guild of<br>Family Healers Oceania</span>
    </div>

    <h2 class="hours-title">Working Hours</h2>
    <table class="hours-table">
      <tr><td class="day">Monday</td><td class="sep">:</td><td class="time">7am - 7pm</td></tr>
      <tr><td class="day">Tuesday</td><td class="sep">:</td><td class="time">7am - 12pm</td></tr>
      <tr><td class="day">Wednesday</td><td class="sep">:</td><td class="time">7am - 10pm</td></tr>
      <tr><td class="day">Thursday</td><td class="sep">:</td><td class="time">7am - 12pm</td></tr>
      <tr><td class="day">Friday</td><td class="sep">:</td><td class="time">7am - 8pm</td></tr>
      <tr><td class="day">Saturday</td><td class="sep">:</td><td class="time">8am - 10pm</td></tr>
      <tr><td class="day">Sunday</td><td class="sep">:</td><td class="time">Off</td></tr>
    </table>

    <div class="contact-band">
      <svg class="contact-icon icon-home" width="30" height="28" viewBox="0 0 30 28" aria-hidden="true">
        <path d="M2 13 L15 2 L28 13" fill="none" stroke="var(--accent-orange)" stroke-width="2.5" stroke-linejoin="round"/>
        <rect x="6" y="12" width="18" height="14" fill="none" stroke="var(--accent-orange)" stroke-width="2.5"/>
        <rect x="9" y="16" width="5" height="4" fill="var(--accent-orange)"/>
        <rect x="17" y="17" width="4" height="9" fill="var(--accent-orange)"/>
      </svg>
      <p class="address">Upper Level, Harbour Walk Arcade, Ridgeview Shopping Centre<br>Ridgeview, NSW 2199</p>

      <svg class="contact-icon icon-phone" width="22" height="22" viewBox="0 0 24 24" aria-hidden="true">
        <path fill="var(--accent-orange)" d="M6.6 10.8c1.4 2.8 3.8 5.1 6.6 6.6l2.2-2.2c.3-.3.7-.4 1-.2 1.1.4 2.3.6 3.6.6.6 0 1 .4 1 1V20c0 .6-.4 1-1 1C10.6 21 3 13.4 3 4c0-.6.4-1 1-1h3.5c.6 0 1 .4 1 1 0 1.3.2 2.5.6 3.6.1.3 0 .7-.2 1z"/>
      </svg>
      <p class="phones"><span>P: 02 5550 1400</span><span>F: 02 5550 1233</span></p>
    </div>
  </section>

</body>
</html>
```